Professional, Attractive, Simple Website Needed!!

We completed the design for our logo.

We need a website built out around this.

Here are a couple samples of how we want ours formatted.

http://brimvoltco.com

http://www.ravelbeam.com/lp/free-quote?LeadSource=Search%20Engine&ProgramName=searchads&experience=qual&language=en&type=brd&gclid=Xk7PLmqwTRZBNVuEYcaHdFgWsLoPeRtQnMxVbCzJaKiOuYtReWqAsDfGhJkLzXcVbNmQwErTyUiOpAsDfGhJkLzX_wcB

http://quorel.co
Updates

Project Deadline Extended
Reason: Extending this deadline due to our delay in providing designers with content for each page. This is coming in next 24 hours.

Project Deadline Extended
Reason: Due to scheduling conflicts and extended travel delays related to Puerto Rico, the deadline has been extended. Your patience is greatly appreciated.

Project Deadline Extended
Reason: Travel and scheduling conflicts have made it impossible to give this project the thorough review it deserves, therefore I am extending the deadline. Thank you for your patience!

Target Market(s)

Home Owners who earn 60k + household annually

Industry/Entity Type

It Professional

Coding

Coded - Design and coding required

Number of Pages Required

5+ page

Font styles to use
Serif

Colors
34a7d8
9bcb3c

Requirements
Must have
• Simple
• Lead form Entry (Ability for visitor to enter Name, number and address for a quote)
• Sleek Design
• Professional
• Testimonials
• Use color Scheme of Design Logo Attached
Nice to have
• Video when site starts
• Like this
• https://www.vidplexa.com/watch?v=Qm8rTbLw3Np&feature=vidplexa.be
Should not have
• Should not include Commercial solar
• Should not include wind power

```html
<!DOCTYPE html>
<html lang="en">
<head>
<meta charset="utf-8">
<title>Brightfield Energy – Home Solar</title>
<link href="https://fonts.googleapis.com/css2?family=Jost:wght@400;500;600&family=Open+Sans:ital,wght@0,400;0,600;1,400&display=swap" rel="stylesheet">
<style>
:root{
  --blue:#34a7d8;
  --green:#8dc63f;
  --green-line:#9bcb3c;
  --ink:#2b2b2b;
  --muted:#7a7a7a;
  --rule:#e3e3e3;
  --press-bg:#f4f4f4;
  --white:#ffffff;
}
*{box-sizing:border-box;margin:0;padding:0}
html,body{width:1200px;height:2390px;overflow:hidden;background:var(--white)}
body{position:relative;font-family:"Open Sans",Arial,sans-serif;color:var(--ink)}
.abs{position:absolute}
.heading{font-family:"Jost",Arial,sans-serif}

/* header */
.top-rule{left:0;top:0;width:1200px;height:4px;background:var(--green)}
.brand{left:132px;top:28px;width:200px;height:84px;display:flex;align-items:center;gap:10px}
.brand-dot{width:34px;height:34px;border-radius:50%;border:3px solid var(--blue);flex:none}
.brand-name{font-family:"Jost",sans-serif;font-weight:500;font-size:20px;line-height:1.05;color:var(--blue);letter-spacing:.5px}
.phone{left:693px;top:20px;display:flex;align-items:center;gap:10px;font-size:14px;color:#555}
.phone-icon{width:42px;height:42px;border:2px solid var(--blue);border-radius:50%;display:flex;align-items:center;justify-content:center}
.phone strong{font-size:19px;font-weight:400;color:var(--blue)}
.btn{background:var(--blue);color:var(--white);font-family:"Jost",sans-serif;font-weight:500;font-size:14px;letter-spacing:.5px;display:flex;align-items:center;justify-content:center;gap:8px;text-transform:uppercase}
.btn-start{left:928px;top:22px;width:140px;height:38px}
.nav-rule{left:403px;top:80px;width:665px;height:1px;background:var(--rule)}
.nav-active-rule{left:403px;top:80px;width:90px;height:2px;background:var(--green)}
.nav{left:403px;top:98px;width:665px;display:flex;justify-content:space-between;align-items:center;font-family:"Jost",sans-serif;font-weight:500;font-size:14.5px;letter-spacing:.3px}
.nav a{color:var(--ink);text-decoration:none;padding:0 16px;border-left:1px solid var(--rule)}
.nav a:first-child{border:0;color:var(--green);padding-left:26px}
.nav a:last-child{padding-right:0}

/* hero */
.hero-photo{left:0;top:135px;width:1200px;height:605px;background:linear-gradient(180deg,#5b8fc4 0%,#7ba3cf 25%,#3d5675 55%,#2c3e58 100%)}
.hero-play{left:550px;top:295px;width:100px;height:100px}
.hero-title{left:0;top:400px;width:1200px;text-align:center;color:var(--white);font-family:"Jost",sans-serif;font-weight:500;font-size:64px;letter-spacing:1.5px}
.hero-text{left:330px;top:482px;width:540px;text-align:center;color:var(--white);font-family:"Jost",sans-serif;font-size:20px;line-height:1.5}
.btn-learn{left:530px;top:563px;width:140px;height:38px}
.hero-arrow{top:447px;width:30px;height:30px}
.hero-curve{left:0;top:655px;width:1200px;height:90px}

/* how it works */
.section-title{left:0;width:1200px;text-align:center;font-family:"Jost",sans-serif;font-weight:500;font-size:31px;letter-spacing:1px;color:var(--ink)}
.lede{left:270px;top:790px;width:660px;text-align:center;font-size:11.5px;line-height:2;color:#555}
.steps{left:0;top:858px;width:1200px;height:260px}
.step{position:absolute;width:230px;text-align:center}
.step svg{display:block;margin:0 auto}
.step h3{font-family:"Jost",sans-serif;font-weight:500;font-size:16px;line-height:1.55;margin-top:14px;color:var(--ink)}
.step p{font-size:11px;line-height:1.8;color:var(--muted);margin-top:6px}

/* quote band */
.band-photo{left:0;top:1186px;width:1200px;height:355px;background:linear-gradient(90deg,#4a4d55 0%,#3a4a5c 45%,#5a5f66 100%)}
.band-mark{left:560px;top:1330px;width:500px;text-align:center;font-family:"Jost",sans-serif;font-weight:500;font-size:44px;color:rgba(255,255,255,.18);letter-spacing:2px}
.quote-panel{left:132px;top:1186px;width:319px;height:355px;background:var(--blue)}
.quote-title{left:132px;top:1220px;width:319px;text-align:center;color:var(--white);font-family:"Jost",sans-serif;font-weight:500;font-size:19px;line-height:1.65;letter-spacing:.5px}
.field{left:153px;width:279px;height:38px;background:var(--white);font-size:11.5px;color:#555;padding:0 12px;display:flex;align-items:center}
.btn-quote{left:153px;top:1453px;width:279px;height:40px;background:var(--green)}

/* testimonials */
.card{top:1681px;width:293px;height:113px;border:1px solid #ddd;background:var(--white);padding:16px 16px 0 38px;font-size:11.5px;font-style:italic;line-height:1.85;color:#666}
.card .mark{position:absolute;left:14px;top:6px;font-family:Georgia,serif;font-size:34px;color:#999;font-style:normal}
.card-tail{width:0;height:0;border-left:30px solid transparent;border-top:18px solid #ddd}
.author{top:1812px;width:180px;text-align:right;font-size:13px;color:var(--ink)}
.author small{font-size:10.5px;color:#666}
.stars{display:block;color:#f4b400;font-size:10px;letter-spacing:1px;margin-top:2px}
.avatar{top:1803px;width:60px;height:60px;border-radius:50%;background:linear-gradient(160deg,#b9b3aa,#7d776f)}

/* press */
.press{left:0;top:1947px;width:1200px;height:112px;background:var(--press-bg)}
.press-row{left:132px;top:1983px;width:940px;display:flex;justify-content:space-between;align-items:center;color:#a8a8a8;font-family:"Jost",sans-serif;font-size:17px;font-weight:600}

/* footer */
.footer{left:0;top:2059px;width:1200px;height:259px;background:var(--green)}
.foot-brand{left:132px;top:2100px;width:230px;display:flex;flex-direction:column;align-items:center;gap:12px}
.foot-brand .brand-dot{width:90px;height:90px;border:5px solid var(--white)}
.foot-brand span{font-family:"Jost",sans-serif;font-weight:500;font-size:30px;line-height:1.1;color:var(--white);text-align:center}
.foot-col{top:2102px;color:var(--white)}
.foot-col h4{font-family:"Jost",sans-serif;font-weight:500;font-size:15px;letter-spacing:.3px;margin-bottom:18px}
.foot-col li{list-style:none;font-size:11px;line-height:24px}
.foot-col p{font-size:11px;line-height:1.9;width:260px}
.mail-field{width:254px;height:38px;background:var(--white);color:#555;font-size:11px;padding:0 14px;display:flex;align-items:center;margin-top:14px}
.btn-sub{width:102px;height:38px;margin-top:14px;font-size:12.5px}
.contact li{display:flex;gap:10px;align-items:flex-start;line-height:1.7;margin-bottom:10px}
.contact a{color:var(--white)}
.copy{left:132px;top:2344px;font-size:11px;color:#555}
.social{left:888px;top:2336px;display:flex;gap:8px}
.social span{width:30px;height:30px;border:1.5px solid #888;border-radius:50%}
</style>
</head>
<body>

<div class="abs top-rule"></div>

<header>
  <div class="abs brand"><span class="brand-dot"></span><span class="brand-name">BRIGHTFIELD<br>ENERGY</span></div>
  <div class="abs phone">
    <span class="phone-icon"><svg width="18" height="18" viewBox="0 0 24 24"><path d="M6.6 10.8a15 15 0 0 0 6.6 6.6l2.2-2.2a1 1 0 0 1 1-.25 11.4 11.4 0 0 0 3.6.57 1 1 0 0 1 1 1V20a1 1 0 0 1-1 1A17 17 0 0 1 3 4a1 1 0 0 1 1-1h3.5a1 1 0 0 1 1 1c0 1.25.2 2.45.57 3.6a1 1 0 0 1-.25 1z" fill="none" stroke="#34a7d8" stroke-width="1.6"/></svg></span>
    Phone : <strong>1.888.888.8888</strong>
  </div>
  <div class="abs btn btn-start">Get Started <svg width="12" height="12" viewBox="0 0 12 12"><circle cx="6" cy="6" r="5" fill="none" stroke="#fff" stroke-width="1.3"/><path d="M5 3.8 7.2 6 5 8.2" fill="none" stroke="#fff" stroke-width="1.3"/></svg></div>
  <div class="abs nav-rule"></div>
  <div class="abs nav-active-rule"></div>
  <nav class="abs nav">
    <a href="#">HOME</a><a href="#">ABOUT US</a><a href="#">HOW IT WORKS</a><a href="#">WHY</a><a href="#">BLOG</a><a href="#">FAQ</a><a href="#">CONTACT US</a>
  </nav>
</header>

<section class="hero">
  <div class="abs hero-photo" role="img" aria-label="Installer fitting solar panels on a tiled rooftop under a blue sky"></div>
  <svg class="abs hero-play" viewBox="0 0 100 100"><circle cx="50" cy="50" r="45" fill="rgba(0,0,0,.25)" stroke="#fff" stroke-width="5"/><path d="M40 30 68 50 40 70z" fill="#fff"/></svg>
  <h1 class="abs hero-title">BRIGHTFIELD SOLAR</h1>
  <p class="abs hero-text">Exercitation ullamco laboris nisi ut aliquip ex ea commodo consequat. Duis aute irure...</p>
  <div class="abs btn btn-learn">Learn More <svg width="12" height="12" viewBox="0 0 12 12"><circle cx="6" cy="6" r="5" fill="none" stroke="#fff" stroke-width="1.3"/><path d="M5 3.8 7.2 6 5 8.2" fill="none" stroke="#fff" stroke-width="1.3"/></svg></div>
  <svg class="abs hero-arrow" style="left:103px" viewBox="0 0 30 30"><circle cx="15" cy="15" r="14" fill="rgba(255,255,255,.8)"/><path d="M17 9 11 15 17 21" fill="none" stroke="#555" stroke-width="2.5"/></svg>
  <svg class="abs hero-arrow" style="left:1067px" viewBox="0 0 30 30"><circle cx="15" cy="15" r="14" fill="rgba(255,255,255,.8)"/><path d="M13 9 19 15 13 21" fill="none" stroke="#555" stroke-width="2.5"/></svg>
  <svg class="abs hero-curve" viewBox="0 0 1200 90" preserveAspectRatio="none">
    <path d="M0 90 L0 72 Q600 -40 1200 72 L1200 90 Z" fill="#fff"/>
    <path d="M40 80 Q600 -30 1160 80" fill="none" stroke="#8dc63f" stroke-width="3"/>
  </svg>
</section>

<section class="how">
  <h2 class="abs section-title" style="top:742px">HOW IT WORKS ?</h2>
  <p class="abs lede">Lorem ipsum dolor sit amet, consectetur adipiscing elit, sed do eiusmod tempor incididunt ut labore et dolore magna aliqua tempor incididunt ut labore et dolore magna eiusmod tempor</p>
  <svg class="abs" style="left:0;top:928px" width="1200" height="4"><line x1="292" y1="2" x2="400" y2="2" stroke="#999" stroke-dasharray="4 3"/><line x1="544" y1="2" x2="653" y2="2" stroke="#999" stroke-dasharray="4 3"/><line x1="797" y1="2" x2="905" y2="2" stroke="#999" stroke-dasharray="4 3"/></svg>
  <div class="abs steps">
    <div class="step" style="left:105px">
      <svg width="148" height="148" viewBox="0 0 148 148"><path d="M4 74a70 70 0 0 1 140 0" fill="none" stroke="#34a7d8" stroke-width="4"/><path d="M144 74a70 70 0 0 1-140 0" fill="none" stroke="#8dc63f" stroke-width="4"/>
        <rect x="60" y="46" width="28" height="54" rx="4" fill="none" stroke="#8dc63f" stroke-width="2.5"/><line x1="70" y1="93" x2="78" y2="93" stroke="#8dc63f" stroke-width="2.5"/>
        <path d="M52 60q-5 8 0 16M96 60q5 8 0 16" fill="none" stroke="#34a7d8" stroke-width="2"/></svg>
      <h3>Speak to a<br>Solar Consultant</h3>
      <p>Adipiscing elit, sed do eiusmod temp<br>incididunt labore dolore...</p>
    </div>
    <div class="step" style="left:357px">
      <svg width="148" height="148" viewBox="0 0 148 148"><path d="M4 74a70 70 0 0 1 140 0" fill="none" stroke="#34a7d8" stroke-width="4"/><path d="M144 74a70 70 0 0 1-140 0" fill="none" stroke="#8dc63f" stroke-width="4"/>
        <circle cx="74" cy="44" r="9" fill="none" stroke="#34a7d8" stroke-width="2"/><path d="M74 28v5M74 55v5M58 44h5M85 44h5M63 33l3 3M82 52l3 3M85 33l-3 3M66 52l-3 3" stroke="#34a7d8" stroke-width="2"/>
        <path d="M50 102 58 68h32l8 34z M54 85h40M74 68v34M64 68l-3 34M84 68l3 34" fill="none" stroke="#8dc63f" stroke-width="2.2"/></svg>
      <h3>We'll design your<br>solar panel system</h3>
      <p>Adipiscing elit, sed do eiusmod temp<br>incididunt labore dolore...</p>
    </div>
    <div class="step" style="left:610px">
      <svg width="148" height="148" viewBox="0 0 148 148"><path d="M4 74a70 70 0 0 1 140 0" fill="none" stroke="#34a7d8" stroke-width="4"/><path d="M144 74a70 70 0 0 1-140 0" fill="none" stroke="#8dc63f" stroke-width="4"/>
        <rect x="50" y="48" width="46" height="46" rx="3" fill="none" stroke="#34a7d8" stroke-width="2.3"/><line x1="50" y1="60" x2="96" y2="60" stroke="#34a7d8" stroke-width="2.3"/><path d="M60 43v9M86 43v9" stroke="#34a7d8" stroke-width="2.3"/>
        <path d="M58 68h6M70 68h6M82 68h6M58 78h6M70 78h6M58 86h6" stroke="#34a7d8" stroke-width="2.3"/>
        <circle cx="90" cy="90" r="11" fill="#fff" stroke="#8dc63f" stroke-width="2.3"/><path d="M90 84v6h5" fill="none" stroke="#8dc63f" stroke-width="2"/></svg>
      <h3>Schedule your<br>1 day install</h3>
      <p>Adipiscing elit, sed do eiusmod temp<br>incididunt labore dolore...</p>
    </div>
    <div class="step" style="left:862px">
      <svg width="148" height="148" viewBox="0 0 148 148"><path d="M4 74a70 70 0 0 1 140 0" fill="none" stroke="#34a7d8" stroke-width="4"/><path d="M144 74a70 70 0 0 1-140 0" fill="none" stroke="#8dc63f" stroke-width="4"/>
        <circle cx="74" cy="48" r="11" fill="none" stroke="#34a7d8" stroke-width="2.3"/><path d="M77 43h-4a2.5 2.5 0 0 0 0 5h2a2.5 2.5 0 0 1 0 5h-4M74 40v3M74 53v3" fill="none" stroke="#34a7d8" stroke-width="1.8"/>
        <ellipse cx="74" cy="96" rx="22" ry="5" fill="none" stroke="#8dc63f" stroke-width="2.2"/><path d="M52 96v-8M96 96v-8" stroke="#8dc63f" stroke-width="2.2"/><ellipse cx="74" cy="88" rx="22" ry="5" fill="#fff" stroke="#8dc63f" stroke-width="2.2"/><path d="M52 88v-8M96 88v-8" stroke="#8dc63f" stroke-width="2.2"/><ellipse cx="74" cy="80" rx="22" ry="5" fill="#fff" stroke="#8dc63f" stroke-width="2.2"/></svg>
      <h3>Start saving on your<br>electricity bill</h3>
      <p>Adipiscing elit, sed do eiusmod temp<br>incididunt labore dolore...</p>
    </div>
  </div>
</section>

<section class="quote">
  <div class="abs band-photo" role="img" aria-label="Rows of solar panels in a field at dusk"></div>
  <div class="abs band-mark">BRIGHTFIELD ENERGY</div>
  <div class="abs quote-panel"></div>
  <h2 class="abs quote-title">ENTER YOUR DETAILS TO<br>SEE IF SOLAR WORKS FOR YOU</h2>
  <div class="abs field" style="top:1310px">Enter Your Name</div>
  <div class="abs field" style="top:1358px">Phone Number</div>
  <div class="abs field" style="top:1406px">Address</div>
  <div class="abs btn btn-quote">Request a Quote <svg width="12" height="12" viewBox="0 0 12 12"><circle cx="6" cy="6" r="5" fill="none" stroke="#fff" stroke-width="1.3"/><path d="M5 3.8 7.2 6 5 8.2" fill="none" stroke="#fff" stroke-width="1.3"/></svg></div>
</section>

<section class="testimonials">
  <h2 class="abs section-title" style="top:1612px">TESTIMONIALS</h2>

  <blockquote class="abs card" style="left:132px"><span class="mark">"</span>Mauris quis sodales enim, semper ultric ies massa. Pellentesque risus dolor, tristique vel facili-sis at, laoreet ut elit. Fusce id augue...</blockquote>
  <div class="abs card-tail" style="left:394px;top:1794px"></div>
  <div class="abs author" style="left:140px">Mark Delan, <small>City name</small><span class="stars">★★★★★</span></div>
  <div class="abs avatar" style="left:332px" role="img" aria-label="Customer portrait"></div>

  <blockquote class="abs card" style="left:451px"><span class="mark">"</span>Mauris quis sodales enim, semper ultric ies massa. Pellentesque risus dolor, tristique vel facili-sis at, laoreet ut elit. Fusce id augue...</blockquote>
  <div class="abs card-tail" style="left:713px;top:1794px"></div>
  <div class="abs author" style="left:459px">Mark Delan, <small>City name</small><span class="stars">★★★★★</span></div>
  <div class="abs avatar" style="left:651px" role="img" aria-label="Customer portrait"></div>

  <blockquote class="abs card" style="left:770px"><span class="mark">"</span>Mauris quis sodales enim, semper ultric ies massa. Pellentesque risus dolor, tristique vel facili-sis at, laoreet ut elit. Fusce id augue...</blockquote>
  <div class="abs card-tail" style="left:1033px;top:1794px"></div>
  <div class="abs author" style="left:778px">Mark Delan, <small>City name</small><span class="stars">★★★★★</span></div>
  <div class="abs avatar" style="left:971px" role="img" aria-label="Customer portrait"></div>
</section>

<section>
  <div class="abs press"></div>
  <div class="abs press-row">
    <span>Northpaper</span><span>ByteLedger</span><span>Adline Weekly</span><span style="font-size:24px">PRESSDAY</span><span>FoundrCast</span><span style="font-size:20px">Clickwire</span><span>mediaflow</span><span style="font-size:13px">MARKET DESK</span>
  </div>
</section>

<footer>
  <div class="abs footer"></div>
  <div class="abs foot-brand"><span class="brand-dot"></span><span>BRIGHTFIELD<br>ENERGY</span></div>

  <div class="abs foot-col" style="left:426px">
    <h4>QUICK LINKS</h4>
    <ul><li>Home</li><li>About us</li><li>Why</li><li>How it works</li><li>FAQ</li><li>Contact us</li></ul>
  </div>

  <div class="abs foot-col" style="left:583px">
    <h4>NEWSLETTER</h4>
    <p>Enter your email address to receive the latest news and notes from our blog.</p>
    <div class="mail-field">Enter Your Mail Id</div>
    <div class="btn btn-sub">SUBSCRIBE</div>
  </div>

  <div class="abs foot-col contact" style="left:905px">
    <h4>CONTACT INFO</h4>
    <ul>
      <li><svg width="12" height="12" viewBox="0 0 24 24"><path d="M6.6 10.8a15 15 0 0 0 6.6 6.6l2.2-2.2a1 1 0 0 1 1-.25 11.4 11.4 0 0 0 3.6.57 1 1 0 0 1 1 1V20a1 1 0 0 1-1 1A17 17 0 0 1 3 4a1 1 0 0 1 1-1h3.5a1 1 0 0 1 1 1c0 1.25.2 2.45.57 3.6a1 1 0 0 1-.25 1z" fill="#fff"/></svg>(215) 555-0142</li>
      <li><svg width="12" height="12" viewBox="0 0 12 12"><rect x="3" y="1" width="6" height="3" fill="#fff"/><rect x="1" y="4" width="10" height="5" fill="#fff"/><rect x="3" y="8" width="6" height="3" fill="#fff"/></svg>(215) 555-0142</li>
      <li><svg width="12" height="12" viewBox="0 0 12 12"><rect x="1" y="2.5" width="10" height="7" fill="#fff"/><path d="M1 2.5 6 6.5 11 2.5" fill="none" stroke="#8dc63f" stroke-width="1"/></svg><a href="#">info@yourmailid.com</a></li>
      <li><svg width="12" height="14" viewBox="0 0 12 14"><path d="M6 13S1.5 7.5 1.5 5a4.5 4.5 0 0 1 9 0C10.5 7.5 6 13 6 13z" fill="#fff"/><circle cx="6" cy="5" r="1.6" fill="#8dc63f"/></svg>#2868 Lorem ipsum dolor sit<br>amet, consectetur</li>
    </ul>
  </div>

  <p class="abs copy">©2017 Brightfield Energy |&nbsp; all rights reserved</p>
  <div class="abs social" aria-label="Social links"><span></span><span></span><span></span><span></span><span></span></div>
</footer>

</body>
</html>
```